Law Firm Folder with 5 step inserts

Square Corners Two Pocket Presentation Folder - inside and outside design with 5 stepped inserts. Please look at website pelvaninjurylaw .com for colors

Target Market(s)

Given to new clients

Industry/Entity Type

legal

Requirements
Must have
• use brand colors.
Nice to have
• would like to include partner photos
Should not have
• not generic

```html
<!DOCTYPE html>
<html lang="en">
<head>
<meta charset="utf-8">
<title>Pelvan &amp; Marlowe – Folder Insert</title>
<link href="https://fonts.googleapis.com/css2?family=Arimo:ital,wght@0,400;0,500;0,700;1,400;1,700&display=swap" rel="stylesheet">
<style>
  :root {
    --gold-light: #f5e27a;
    --gold-mid: #c9a233;
    --gold-dark: #a8801e;
    --gold-line: #b89a45;
    --navy-top: #405b78;
    --navy-mid: #1f3049;
    --navy-bottom: #101a29;
    --button-fill: #28354a;
    --text-main: #ffffff;
    --text-soft: #e8edf3;
  }
  * { box-sizing: border-box; margin: 0; padding: 0; }
  html, body { width: 849px; height: 1200px; overflow: hidden; }
  body { font-family: "Arimo", Helvetica, Arial, sans-serif; color: var(--text-main); }
  .insert {
    position: relative; width: 849px; height: 1200px; overflow: hidden;
    background: linear-gradient(180deg, var(--navy-top) 0%, var(--navy-mid) 45%, var(--navy-bottom) 100%);
  }
  .gold-band {
    position: absolute; left: 0; width: 100%;
    background: linear-gradient(90deg, var(--gold-dark) 0%, var(--gold-light) 28%, var(--gold-mid) 55%, var(--gold-light) 80%, var(--gold-dark) 100%);
  }
  .gold-band--top { top: 0; height: 21px; }
  .gold-band--bottom { bottom: 0; height: 26px; }
  .team-photo {
    position: absolute; left: 34px; top: 52px; width: 782px; height: 309px;
    background: linear-gradient(180deg, #b9a86a 0%, #8a6a45 45%, #6b3a22 75%, #4a2a1f 100%);
    box-shadow: 4px 5px 8px rgba(0,0,0,.55);
  }
  .intro-frame {
    position: absolute; left: 16px; top: 389px; width: 819px; height: 378px;
    border: 1.5px solid var(--gold-line); border-top: none;
  }
  .frame-top { position: absolute; left: 16px; top: 383px; width: 819px; height: 12px; }
  .intro-title {
    position: absolute; top: 378px; left: 0; width: 849px; text-align: center;
    font-size: 23px; font-weight: 700; font-style: italic;
  }
  .intro-copy {
    position: absolute; left: 30px; top: 429px; width: 800px;
    font-size: 15.2px; font-style: italic; line-height: 19.4px; color: var(--text-soft);
  }
  .intro-copy p { margin-bottom: 12px; }
  .client-list { list-style: none; margin: 4px 0 12px; }
  .client-list li { display: flex; align-items: flex-end; height: 19.4px; }
  .client-list svg { width: 20px; height: 18px; margin-right: 3px; }
  .locations-title {
    position: absolute; top: 784px; left: 0; width: 849px; text-align: center;
    font-size: 23px; font-weight: 700; font-style: italic;
  }
  .locations-intro {
    position: absolute; left: 119px; top: 816px; width: 600px;
    font-size: 15.2px; font-style: italic; line-height: 19.4px; color: var(--text-soft);
  }
  .location-grid {
    position: absolute; left: 108px; top: 877px; width: 622px;
    display: grid; grid-template-columns: 270px 270px; column-gap: 82px; row-gap: 27px;
  }
  .location-button {
    height: 47px; background: var(--button-fill); display: flex; align-items: center; justify-content: center;
    font-size: 23px; font-weight: 500; box-shadow: 3px 4px 5px rgba(0,0,0,.45);
  }
</style>
</head>
<body>
<main class="insert">
  <div class="gold-band gold-band--top"></div>

  <div class="team-photo" role="img" aria-label="Photo of the firm's attorneys and staff seated around a polished conference table"></div>

  <svg class="frame-top" viewBox="0 0 819 12" aria-hidden="true">
    <line x1="0" y1="6" x2="229" y2="6" stroke="#b89a45" stroke-width="1.5"/>
    <circle cx="229" cy="6" r="3" fill="#b89a45"/>
    <circle cx="569" cy="6" r="3" fill="#b89a45"/>
    <line x1="569" y1="6" x2="819" y2="6" stroke="#b89a45" stroke-width="1.5"/>
  </svg>
  <div class="intro-frame"></div>
  <h2 class="intro-title">Lorem ipsum dolor sit amet</h2>

  <div class="intro-copy">
    <p>The legal process can be overwhelming. Too often, victims of negligence shy away from pursuing legal action even when they rightfully deserve compensation for their injuries. You may be facing pain, disability, and time away from work that you and your family simply can’t afford. Our Florida injury attorneys are dedicated to understanding the unique details of your case and providing clear and honest counsel.</p>
    <p>Through care, communication, and a commitment to excellence, Pelvan &amp; Marlowe takes the stress out of your legal matters so you can focus on healing. It has been our honor to serve a variety of clients, including:</p>
    <ul class="client-list">
      <li><svg viewBox="0 0 20 18"><path d="M1 11 L6 16 L19 1" fill="none" stroke="#b89a45" stroke-width="1.8"/></svg>Drivers</li>
      <li><svg viewBox="0 0 20 18"><path d="M1 11 L6 16 L19 1" fill="none" stroke="#b89a45" stroke-width="1.8"/></svg>Property Owners</li>
      <li><svg viewBox="0 0 20 18"><path d="M1 11 L6 16 L19 1" fill="none" stroke="#b89a45" stroke-width="1.8"/></svg>Businesses</li>
      <li><svg viewBox="0 0 20 18"><path d="M1 11 L6 16 L19 1" fill="none" stroke="#b89a45" stroke-width="1.8"/></svg>Professionals</li>
      <li><svg viewBox="0 0 20 18"><path d="M1 11 L6 16 L19 1" fill="none" stroke="#b89a45" stroke-width="1.8"/></svg>Employers</li>
    </ul>
    <p>This is your case and your life. Your voice is essential to our process. We are proud to advocate on your behalf, and we will do everything within the law to obtain the justice you deserve.</p>
  </div>

  <h2 class="locations-title">Out Location</h2>
  <p class="locations-intro">Lorem ipsum dolor sit amet, consectetuer adipiscing elit, sed diam nonummy nibh euismod tincidunt ut laoreet dolore magna aliquam erat volutpat. Ut wisi enim ad</p>

  <nav class="location-grid">
    <div class="location-button">Boca Raton</div>
    <div class="location-button">Boyn Beach</div>
    <div class="location-button">Delray Beach</div>
    <div class="location-button">Ft. Lauderdale</div>
    <div class="location-button">Palm Bay</div>
    <div class="location-button">Stuart</div>
    <div class="location-button">Vero Beach</div>
    <div class="location-button">West Palm Beach</div>
  </nav>

  <div class="gold-band gold-band--bottom"></div>
</main>
</body>
</html>
```